Business Card Design for Occupational Medicine Start Up Company

We need to design a professional business card. We are a healthcare company providing occupational medicine services to blue collar industries. We are professional, efficient and high quality service providers.

Target Market(s)

Blue Collar Industry: Shipbuilding, Ports, Trucking Companies; The Executives and Safety Officers for these companies

Industry/Entity Type

Healthcare

Contact Information for Business Card

Logo, Name, Title, Email, Phone

Other font styles liked:
• Please match our Brand Guide

Requirements
Must have
• Our Company Colors and Logo

```html
<!DOCTYPE html>
<html lang="en">
<head>
<meta charset="utf-8">
<title>CrewWell Business Card</title>
<link href="https://fonts.googleapis.com/css2?family=Montserrat:wght@600;700&family=Roboto:wght@400&display=swap" rel="stylesheet">
<style>
  :root {
    --backdrop: #141414;
    --card: #262626;
    --card-deep: #1c1c1c;
    --brand-blue: #2b3a8f;
    --brand-sky: #2fa3e0;
    --brand-amber: #f5a83a;
    --ink-light: #f2f2f2;
  }
  * { margin: 0; padding: 0; box-sizing: border-box; }
  html, body {
    width: 1200px; height: 900px; overflow: hidden;
    background: var(--backdrop);
  }
  .stage {
    position: relative; width: 1200px; height: 900px;
    display: flex; flex-direction: column; align-items: center; justify-content: center; gap: 44px;
  }
  .card {
    position: relative; width: 620px; height: 354px;
    background: linear-gradient(160deg, var(--card) 0%, var(--card-deep) 100%);
    border-bottom: 6px solid var(--brand-blue);
    overflow: hidden;
  }
  /* back side */
  .card-back .brand-pattern {
    position: absolute; inset: 0;
    background: linear-gradient(100deg, #161616 0%, #2a2a2a 60%, #3a3a3a 100%);
  }
  .card-back .corner-mark {
    position: absolute; right: 78px; bottom: 58px;
    width: 38px; height: 38px; border-radius: 50%;
    background: var(--brand-amber);
  }
  /* front side */
  .card-front .brand {
    position: absolute; left: 48px; top: 0; bottom: 0; width: 255px;
    display: flex; align-items: center; justify-content: center; gap: 12px;
  }
  .brand-dot {
    width: 20px; height: 20px; border-radius: 50%; background: var(--brand-sky);
  }
  .brand-name {
    font-family: "Montserrat", sans-serif; font-weight: 700;
    font-size: 36px; letter-spacing: 1px; color: var(--brand-blue);
  }
  .divider {
    position: absolute; left: 326px; top: 112px;
    width: 3px; height: 128px; background: var(--brand-amber);
  }
  .contact {
    position: absolute; left: 352px; top: 112px;
    font-family: "Roboto", sans-serif; color: var(--ink-light);
  }
  .person-name {
    font-family: "Montserrat", sans-serif; font-weight: 700;
    font-size: 24px; color: var(--brand-blue); letter-spacing: 0.5px;
    text-transform: uppercase; line-height: 1;
  }
  .person-title { font-size: 17px; margin-top: 6px; margin-bottom: 16px; }
  .contact-list { list-style: none; font-size: 18px; line-height: 27px; }
  .contact-list li { display: flex; align-items: center; gap: 7px; }
  .contact-list svg { width: 14px; height: 14px; flex: none; }
</style>
</head>
<body>
<main class="stage">
  <section class="card card-back">
    <div class="brand-pattern" role="img" aria-label="Repeating brand mark pattern in glossy black"></div>
    <span class="corner-mark"></span>
  </section>

  <section class="card card-front">
    <div class="brand">
      <span class="brand-dot"></span>
      <span class="brand-name">CREWWELL</span>
    </div>
    <span class="divider"></span>
    <div class="contact">
      <p class="person-name">Daniel Harper</p>
      <p class="person-title">Director</p>
      <ul class="contact-list">
        <li>
          <svg viewBox="0 0 24 24" aria-hidden="true"><path fill="#2fa3e0" d="M6.6 10.8a15.1 15.1 0 0 0 6.6 6.6l2.2-2.2a1 1 0 0 1 1-.25 11.4 11.4 0 0 0 3.6.57 1 1 0 0 1 1 1V20a1 1 0 0 1-1 1A17 17 0 0 1 3 4a1 1 0 0 1 1-1h3.5a1 1 0 0 1 1 1c0 1.25.2 2.45.57 3.57a1 1 0 0 1-.25 1z"/></svg>
          (480)555 0142
        </li>
        <li>
          <svg viewBox="0 0 24 24" aria-hidden="true"><rect x="2" y="5" width="20" height="14" rx="1.5" fill="#2b3a8f"/><path d="M3 6l9 7 9-7" fill="none" stroke="#f2f2f2" stroke-width="1.5"/></svg>
          hello@crewwellmed.com
        </li>
        <li>
          <svg viewBox="0 0 24 24" aria-hidden="true"><g fill="none" stroke="#2b3a8f" stroke-width="2"><circle cx="12" cy="12" r="9"/><ellipse cx="12" cy="12" rx="4" ry="9"/><path d="M3 12h18"/></g></svg>
          www.crewwellmed.com
        </li>
      </ul>
    </div>
  </section>
</main>
</body>
</html>
```